Financial Services Consultant needs a business card

We need a business card for a new consulting company based in Melbourne called
"Quelbrook Insights". Tagline is Assess, Track, Improve
We would like to see business card designs that are in line with the minimal style of the website www.quelbrook-insights.example
The font I have used on the website is Proxima Nova and would like the same or similar font used on the business card with a minimal design in line with the website Two sided with "QUELBROOK INSIGHTS" ASSESS, TRACK, IMPROVE on one side and name, title and contact details on the otther
Updates

Hi All, thanks for your submissions, much appreciated.

I have recently added some colour to my webiste, it is hex #3a7b74 for those that wish to use it
Thanks

Hi all

thanks very much for your design submissions I am very impressed and they are much appreciated.

Interms of general feedback please find below;

Colour: I am trying to stick to a minimal design and colour scheme for my website which is still under construction, up to 3 colours( www.quelbrook-insights.example) it is currently black and white with a small amount of blue/green but I am open to suggestion/interpretations for a consulting company.

Card: I dont mind if it has rounded edges or straight, I was thinking about using a letterpress card if possible

Detail: the detail on the card will include; Name, Title, Mobile, Personal Email, Business Email,Web,Business Address

Once again thanks for submissions

Industry/Entity Type

Business

```html
<!DOCTYPE html>
<html lang="en">
<head>
<meta charset="utf-8">
<title>Quelbrook Insights — Business Card</title>
<link rel="stylesheet" href="https://fonts.googleapis.com/css2?family=Montserrat:wght@600;700&family=Open+Sans:wght@400;600;700&display=swap">
<style>
  :root {
    --page-bg: #e9e7e3;
    --card-bg: #ffffff;
    --ink: #111111;
    --band: #1a1717;
    --band-text: #f2f2f2;
    --muted: #3c3c3c;
    --frame: #c9c9c9;
    --teal: #3a7b74;
    --card-shadow: 0 6px 18px rgba(0, 0, 0, 0.18);
  }

  * { box-sizing: border-box; margin: 0; padding: 0; }

  html, body {
    width: 1200px;
    height: 720px;
    overflow: hidden;
  }

  body {
    background: var(--page-bg);
    display: flex;
    align-items: center;
    justify-content: center;
    gap: 36px;
    font-family: "Open Sans", Arial, sans-serif;
    color: var(--ink);
  }

  .card {
    position: relative;
    width: 560px;
    height: 320px;
    background: var(--card-bg);
    box-shadow: var(--card-shadow);
    overflow: hidden;
  }

  .wordmark {
    display: inline-block;
    padding: 4px 8px;
    border: 1px solid var(--frame);
    font-family: "Montserrat", Arial, sans-serif;
    font-weight: 700;
    font-size: 26px;
    letter-spacing: 3px;
    line-height: 1.2;
    color: var(--ink);
    white-space: nowrap;
  }

  /* Contact side */
  .contact-head {
    position: absolute;
    top: 74px;
    left: 0;
    right: 0;
    text-align: center;
  }

  .contact-band {
    position: absolute;
    top: 136px;
    left: 0;
    right: 0;
    height: 96px;
    background: var(--band);
    color: var(--band-text);
    display: flex;
    align-items: center;
    justify-content: center;
    font-size: 13px;
    line-height: 1.6;
  }

  .contact-address {
    font-style: normal;
    text-align: right;
    padding-right: 14px;
  }

  .contact-divider {
    width: 1px;
    height: 46px;
    background: var(--band-text);
    opacity: 0.7;
  }

  .contact-lines {
    padding-left: 14px;
    list-style: none;
  }

  .contact-lines li {
    display: flex;
    align-items: center;
    gap: 7px;
  }

  .contact-icon {
    width: 12px;
    height: 12px;
    flex: none;
  }

  .person {
    position: absolute;
    top: 250px;
    left: 0;
    right: 0;
    text-align: center;
    font-size: 16px;
    font-weight: 600;
    color: var(--muted);
  }

  .person-title {
    font-weight: 400;
    color: var(--teal);
  }

  /* Brand side */
  .brand-lockup {
    position: absolute;
    top: 100px;
    left: 50%;
    transform: translateX(-50%);
    display: flex;
    flex-direction: column;
    align-items: flex-end;
  }

  .tagline {
    margin-top: 8px;
    font-size: 15px;
    color: var(--muted);
    letter-spacing: 0.3px;
  }

  .web-address {
    position: absolute;
    top: 236px;
    left: 0;
    right: 0;
    text-align: center;
    font-size: 15px;
    letter-spacing: 3px;
    color: var(--muted);
  }

  .web-address strong {
    font-weight: 700;
    color: var(--ink);
  }
</style>
</head>
<body>

  <section class="card card--contact" aria-label="Contact side">
    <div class="contact-head">
      <div class="wordmark">QUELBROOK INSIGHTS</div>
    </div>

    <div class="contact-band">
      <address class="contact-address">
        Street Name, City Name<br>
        State Zip Code
      </address>
      <div class="contact-divider"></div>
      <ul class="contact-lines">
        <li>
          <svg class="contact-icon" viewBox="0 0 12 12" aria-hidden="true">
            <circle cx="6" cy="6" r="5.5" fill="none" stroke="currentColor" stroke-width="1"/>
            <path d="M4 3.2 L5 3 L5.6 4.6 L5 5.2 Q5.6 6.6 6.8 7 L7.4 6.4 L9 7 L8.8 8 Q6.8 8.8 5 7 Q3.4 5.2 4 3.2 Z" fill="currentColor"/>
          </svg>
          123-456-0789
        </li>
        <li>
          <svg class="contact-icon" viewBox="0 0 12 12" aria-hidden="true">
            <circle cx="6" cy="6" r="5.5" fill="none" stroke="currentColor" stroke-width="1"/>
            <ellipse cx="6" cy="6" rx="2.3" ry="5.5" fill="none" stroke="currentColor" stroke-width="0.8"/>
            <line x1="0.5" y1="6" x2="11.5" y2="6" stroke="currentColor" stroke-width="0.8"/>
          </svg>
          www.quelbrook-insights.example
        </li>
      </ul>
    </div>

    <p class="person">Your Name, <span class="person-title">Title</span></p>
  </section>

  <section class="card card--brand" aria-label="Brand side">
    <div class="brand-lockup">
      <div class="wordmark">QUELBROOK INSIGHTS</div>
      <p class="tagline">Assess, Track, Improve</p>
    </div>

    <p class="web-address">www.<strong>quelbrook-insights</strong>.example</p>
  </section>

</body>
</html>
```